Upmarket Dessert Lounge needs a Business Card Design

We are an upmarket dessert lounge needing a business card to match our image.

We want something that is simple yet beautiful, feminine, classy, sophisticated and elegant. We want it to stand out and don't mind if it is bold.

The design should include our logo and colours of red or maroon with gold highlights. We don't mind if black is used.

Marlow & Quince

Target Market(s)

For those who like to indulge or treat themselves and give in to their temptations on good quality desserts.

Industry/Entity Type

Business

Requirements
Must have
• Must include our logo and our name

Marlow & Quince

M & Q

```html
<!DOCTYPE html>
<html lang="en">
<head>
<meta charset="utf-8">
<title>Marlow &amp; Quince — Business Card</title>
<link rel="stylesheet" href="https://fonts.googleapis.com/css2?family=Tinos:wght@400;700&display=swap">
<style>
  :root {
    --backdrop: #ece8e3;
    --card: #ffffff;
    --maroon: #7a1418;
    --gold: #f7cf98;
    --black: #000000;
    --ink: #4a4a4a;
    --white: #ffffff;
  }
  * { box-sizing: border-box; margin: 0; padding: 0; }
  html, body { width: 1200px; height: 417px; overflow: hidden; background: var(--backdrop); }
  body { position: relative; font-family: "Tinos", "Times New Roman", serif; }

  .card {
    position: absolute;
    top: 61px;
    width: 515px;
    height: 294px;
    background: var(--card);
    overflow: hidden;
    box-shadow: 0 2px 6px rgba(0,0,0,.25);
  }
  .card--front { left: 54px; }
  .card--back { left: 630px; }

  .swoosh { position: absolute; inset: 0; width: 100%; height: 100%; }

  .brand-name {
    position: absolute;
    color: var(--maroon);
    font-weight: 400;
    font-size: 27px;
    letter-spacing: 0.5px;
    white-space: nowrap;
    transform: translate(-50%, -50%);
  }
  .card--front .brand-name { left: 170px; top: 132px; }
  .card--back .brand-name { left: 258px; top: 118px; }

  .contact {
    position: absolute;
    left: 338px;
    top: 72px;
    color: var(--ink);
    font-size: 13.5px;
    line-height: 18px;
  }
  .contact__address { margin-bottom: 6px; }
  .contact__list { list-style: none; }
  .contact__item { display: flex; align-items: center; gap: 7px; height: 20.5px; }
  .contact__icon { width: 9px; height: 9px; flex: none; }

  .holder {
    position: absolute;
    right: 60px;
    bottom: 16px;
    color: var(--gold);
    font-size: 17px;
    font-weight: 700;
  }
  .holder__title { font-weight: 400; font-size: 14px; }

  .web {
    position: absolute;
    left: 250px;
    bottom: 20px;
    color: var(--white);
    font-size: 14.5px;
    letter-spacing: 2.6px;
  }
</style>
</head>
<body>

<section class="card card--front" aria-label="Card front">
  <svg class="swoosh" viewBox="0 0 525 300" preserveAspectRatio="none" aria-hidden="true">
    <path fill="var(--maroon)" d="M0 128 C0 200 55 246 250 238 C90 236 20 205 0 160 Z"/>
    <path fill="var(--gold)" d="M18 218 C60 252 150 258 250 240 C340 222 420 200 512 222 C420 212 340 232 250 250 C150 268 60 258 18 218 Z"/>
    <path fill="var(--black)" d="M0 178 C12 240 60 268 140 268 C260 268 330 238 440 238 C478 238 505 258 525 300 L0 300 Z"/>
  </svg>

  <p class="brand-name">MARLOW &amp; QUINCE</p>

  <div class="contact">
    <p class="contact__address">00, Complex name<br>City, State 000 000</p>
    <ul class="contact__list">
      <li class="contact__item">
        <svg class="contact__icon" viewBox="0 0 10 10"><circle cx="5" cy="5" r="5" fill="var(--maroon)"/><path d="M3 3 L4.5 3 L4.5 4 L3.8 4.6 Q4.5 6 5.6 6.4 L6.2 5.6 L7.2 5.6 L7.2 7 Q4 7.4 3 3 Z" fill="#fff"/></svg>
        +1 555 014 2207
      </li>
      <li class="contact__item">
        <svg class="contact__icon" viewBox="0 0 10 10"><rect x="2" y="0" width="6" height="10" rx="1" fill="var(--maroon)"/><rect x="3" y="1.5" width="4" height="4" fill="#fff"/></svg>
        +1 555 014 2207
      </li>
      <li class="contact__item">
        <svg class="contact__icon" viewBox="0 0 10 10"><rect x="0" y="2" width="10" height="6.5" fill="var(--maroon)"/><path d="M0.5 2.5 L5 5.8 L9.5 2.5" stroke="#fff" stroke-width="0.9" fill="none"/></svg>
        info@marlowquince.com
      </li>
      <li class="contact__item">
        <svg class="contact__icon" viewBox="0 0 10 10"><circle cx="5" cy="5" r="5" fill="var(--maroon)"/><path d="M0 5 H10 M5 0 Q2 5 5 10 M5 0 Q8 5 5 10" stroke="#fff" stroke-width="0.8" fill="none"/></svg>
        www.marlowquince.com
      </li>
    </ul>
  </div>

  <p class="holder">YOUR NAME, <span class="holder__title">Title</span></p>
</section>

<section class="card card--back" aria-label="Card back">
  <svg class="swoosh" viewBox="0 0 525 300" preserveAspectRatio="none" aria-hidden="true">
    <path fill="var(--maroon)" d="M0 128 C0 200 55 246 250 238 C90 236 20 205 0 160 Z"/>
    <path fill="var(--gold)" d="M18 218 C60 252 150 258 250 240 C340 222 420 200 512 222 C420 212 340 232 250 250 C150 268 60 258 18 218 Z"/>
    <path fill="var(--black)" d="M0 178 C12 240 60 268 140 268 C260 268 330 238 440 238 C478 238 505 258 525 300 L0 300 Z"/>
  </svg>

  <p class="brand-name">MARLOW &amp; QUINCE</p>

  <p class="web">www.marlowquince.com</p>
</section>

</body>
</html>
```